Design a web site for my business - Brightline Coatings Co.

We are a family business that handles design, fabrication and installation of powder coated aluminum, stainless steel and glass products. Including handrails, privacy slat screens, electric gates and pool fencing. We are based in the Whitsundays in North Queensland and service an area from Airlie Beach to Townsville.

Target Market(s)

Domestic and commercial

Industry/Entity Type

fabrication - manufacturing

Coding

Coded - Design and coding required

Number of Pages Required

5+ page

Colors
0054AA
0677BA
7BADD7
CADEEF
E8F1F8

Requirements
Must have
• photo galleries, contact page, one page for privacy screens, balustrades, glass fencing, stainless steel handrail, powder coated aluminium handrails and pool fencing

```html
<!DOCTYPE html>
<html lang="en">
<head>
<meta charset="utf-8">
<title>Brightline Coatings Co — Quality Fabrication</title>
<link href="https://fonts.googleapis.com/css2?family=Poppins:wght@400;500;600;700&display=swap" rel="stylesheet">
<style>
:root{
  --navy:#0a2466;
  --navy-deep:#0b1d45;
  --navy-darkest:#081734;
  --blue:#0054AA;
  --blue-mid:#0677BA;
  --blue-soft:#7BADD7;
  --blue-pale:#CADEEF;
  --blue-mist:#E8F1F8;
  --ink:#1b2440;
  --white:#ffffff;
  --line:#dfe6ef;
}
*{box-sizing:border-box;margin:0;padding:0}
html,body{width:1200px;height:2890px;overflow:hidden}
body{font-family:"Poppins",sans-serif;color:var(--ink);background:var(--white);position:relative}
section,header,footer,div{position:relative}
.abs{position:absolute}
svg{display:block}

/* top bar */
.topbar{height:36px;background:var(--navy);color:var(--white);font-size:11px;display:flex;align-items:center;padding:0 34px}
.topbar .contact{margin-left:auto;display:flex;gap:18px;align-items:center}
.topbar .contact span{display:flex;align-items:center;gap:6px}
.social-square{width:13px;height:13px;background:var(--white);border-radius:2px}

/* nav */
.nav{height:71px;display:flex;align-items:center;padding:0 34px;border-bottom:1px solid var(--line)}
.brand{display:flex;align-items:center;gap:10px}
.brand-mark{width:34px;height:34px;border-radius:50%;background:var(--blue-pale)}
.brand-name{font-size:11px;font-weight:600;color:#5d6678;letter-spacing:.5px}
.menu{display:flex;gap:46px;margin-left:260px;font-size:12.5px;font-weight:500;color:var(--ink)}
.menu .active{color:var(--blue)}
.btn-quote-nav{margin-left:auto;background:var(--navy);color:var(--white);font-size:12.5px;font-weight:600;padding:11px 27px;border-radius:3px}

/* hero */
.hero{height:521px;color:var(--white);overflow:hidden}
.hero-photo{position:absolute;inset:0;background:linear-gradient(90deg,#1f2a22 0%,#2f3b2c 35%,#55654a 60%,#7d8d6c 80%,#9aa884 100%)}
.hero-photo::after{content:"";position:absolute;inset:0;background:linear-gradient(90deg,rgba(20,26,20,.85) 0%,rgba(20,26,20,.5) 45%,rgba(20,26,20,0) 75%)}
.eyebrow-hero{left:35px;top:36px;font-size:17px;font-weight:600}
.hero h1{left:34px;top:62px;font-size:46px;font-weight:700;letter-spacing:.5px}
.hero h1 .accent{color:var(--blue-soft)}
.rule{width:58px;height:3px;background:var(--blue)}
.rule.light{background:var(--blue-soft)}
.hero .rule{left:35px;top:133px}
.hero-copy{left:35px;top:160px;width:410px;font-size:14px;line-height:25px}
.btn{display:inline-flex;align-items:center;gap:10px;font-size:12.5px;font-weight:600;border-radius:2px;white-space:nowrap}
.btn-solid{background:var(--blue);color:var(--white)}
.btn-outline{border:1px solid var(--white);color:var(--white)}
.hero .btn{top:303px;height:37px;padding:0 18px}
.features{left:34px;top:430px;display:flex}
.feature{display:flex;gap:14px;padding-right:18px;margin-right:20px;border-right:1px solid rgba(255,255,255,.6);height:46px}
.feature:last-child{border:none}
.feature h4{font-size:10.5px;font-weight:600;margin-bottom:4px;white-space:nowrap}
.feature p{font-size:10px;line-height:14px;opacity:.9;white-space:nowrap}
.local-card{left:949px;top:393px;width:233px;height:84px;background:var(--navy);border-radius:3px;padding:14px 16px;display:flex;gap:14px}
.local-card h4{font-size:12px;font-weight:500;margin-bottom:6px}
.local-card p{font-size:10px;line-height:18px}

/* products */
.products{height:378px}
.eyebrow{font-size:13px;font-weight:600;color:var(--blue)}
.title{font-size:19.5px;font-weight:700;color:var(--navy);line-height:24px}
.products .intro{left:33px;top:44px;width:275px}
.products .intro .title{margin-top:14px}
.products .intro .rule{margin:18px 0 16px;width:36px;height:2px}
.products .intro p{font-size:13px;line-height:25px}
.products .intro .btn{margin-top:24px;height:36px;padding:0 18px}
.card{top:40px;width:251px;height:300px;border:1px solid var(--line);border-radius:3px;text-align:center;background:var(--white)}
.card-photo{height:154px}
.card h3{font-size:13.5px;font-weight:600;color:var(--navy);margin-top:18px}
.card p{font-size:12px;line-height:20px;margin:8px auto 0;width:165px}
.card .more{display:inline-flex;align-items:center;gap:8px;font-size:11.5px;font-weight:600;color:var(--blue);margin-top:8px}

/* stats band */
.stats{height:138px;overflow:hidden}
.stats-photo{position:absolute;inset:0;background:linear-gradient(90deg,#3a4a3f,#5f6e62 40%,#77806e)}
.stats-navy{position:absolute;inset:0;background:var(--navy);clip-path:polygon(0 0,795px 0,750px 100%,0 100%)}
.stats-shade{position:absolute;inset:0;background:linear-gradient(90deg,rgba(10,36,102,0) 60%,rgba(10,36,102,.65) 75%,rgba(10,36,102,.75))}
.stat{top:18px;color:var(--white)}
.stat .num{font-size:27px;font-weight:500;line-height:30px}
.stat .label{font-size:11px;font-weight:600;color:var(--blue-soft);margin:4px 0 6px}
.stat p{font-size:12px;line-height:16px}
.stat-divider{top:28px;width:1px;height:86px;background:rgba(255,255,255,.5)}
.ready{left:846px;top:26px;color:var(--white)}
.ready h3{font-size:16px;font-weight:600}
.ready p{font-size:10.5px;margin-top:2px}
.ready .btn{height:35px;padding:0 16px;margin-top:12px;font-size:12px}
.ready .btn-white{background:var(--white);color:var(--blue)}

/* serving */
.serving{height:138px;background:var(--blue-mist);text-align:center}
.serving h4{position:absolute;top:40px;left:0;right:0;font-size:12.5px;font-weight:600;color:var(--navy)}
.badges-row{position:absolute;top:73px;left:0;right:0;display:flex;justify-content:center;gap:30px;align-items:center;font-size:8.5px;color:#44506a}
.badges-row span{display:flex;align-items:center;gap:6px}
.badge-shape{width:24px;height:24px;border-radius:50%;background:var(--blue-mid);display:block}
.badge-square{width:22px;height:22px;background:var(--navy);display:block}
.corvane{display:flex;flex-direction:column;line-height:11px;text-align:left}
.corvane b{font-size:14px;font-weight:600;color:var(--navy)}
.corvane small{font-size:7.5px;color:var(--blue-mid)}

/* about */
.about{height:268px;overflow:hidden}
.about-photo{position:absolute;inset:0;background:linear-gradient(90deg,#ffffff 0%,#ffffff 32%,#b9c4b8 50%,#7c8c75 70%,#9da58f 100%)}
.about-text{left:33px;top:28px;width:460px}
.about-text .title{font-size:19.5px;margin-top:8px}
.about-text .title .blue{color:var(--blue)}
.about-text .rule{width:36px;height:2px;margin:16px 0 18px}
.about-text p{font-size:12.5px;line-height:20px;margin-bottom:12px}

/* process */
.process{height:343px;background:var(--navy);color:var(--white);text-align:center}
.process .eyebrow{position:absolute;top:52px;left:0;right:0;color:var(--white);font-size:13px}
.process h2{position:absolute;top:78px;left:0;right:0;font-size:19.5px;font-weight:600;text-align:center;padding-left:50px}
.step{top:133px;width:220px;margin-left:-110px}
.step-circle{width:67px;height:67px;border-radius:50%;border:1px solid rgba(255,255,255,.6);margin:0 auto;display:flex;align-items:center;justify-content:center}
.step-num{width:23px;height:23px;border-radius:50%;background:var(--white);color:var(--navy);font-size:10.5px;font-weight:700;display:flex;align-items:center;justify-content:center;margin:-13px auto 0}
.step h3{font-size:15px;font-weight:600;margin-top:10px;letter-spacing:.3px}
.step p{font-size:12px;line-height:20px;margin-top:10px}

/* cta */
.cta{height:312px;overflow:hidden}
.cta-photo{position:absolute;inset:0;background:linear-gradient(90deg,var(--blue-mist) 0%,var(--blue-mist) 40%,#cfdbe6 70%,#b4c6d4 100%)}
.cta-text{left:33px;top:43px;width:380px}
.cta-text .title{font-size:19.5px}
.cta-text .title .blue{color:var(--blue)}
.cta-text .rule{width:36px;height:2px;margin:14px 0 18px}
.cta-text p{font-size:13px;line-height:20px}
.cta .btn{top:95px;height:45px;font-size:15px;padding:0 22px;gap:12px}
.btn-outline-blue{border:1px solid var(--blue);color:var(--blue)}
.cta-feats{left:616px;top:220px;display:flex;align-items:center;font-size:13px;font-weight:600;color:var(--navy);white-space:nowrap}
.cta-feats span{display:flex;align-items:center;gap:8px;padding:0 16px;border-right:2px solid var(--blue)}
.cta-feats span:first-child{padding-left:0}
.cta-feats span:last-child{border:none;padding-right:0}

/* footer */
.footer{height:549px;background:var(--navy-deep);color:var(--white)}
.f-col{top:50px}
.f-divider{top:50px;width:1px;height:450px;background:rgba(255,255,255,.2)}
.f-brand-name{font-size:17px;font-weight:700;letter-spacing:.3px;margin-top:14px;white-space:nowrap}
.f-brand-sub{font-size:12px;color:var(--blue-soft);letter-spacing:1px}
.f-mark{width:84px;height:84px;border-radius:50%;background:var(--blue-mid)}
.footer .rule{width:38px;height:2px;margin:20px 0 22px;background:var(--blue)}
.f-about{font-size:12px;line-height:25px}
.f-about p{margin-bottom:16px}
.f-socials{display:flex;gap:20px;margin-top:18px}
.f-socials i{width:21px;height:21px;background:var(--white);border-radius:3px;display:block}
.footer h4{font-size:14.5px;font-weight:600;letter-spacing:.3px}
.f-links{list-style:none;margin-top:24px;width:240px}
.f-links li{font-size:12px;padding:12px 0;border-bottom:1px solid rgba(255,255,255,.2);display:flex;justify-content:space-between}
.f-links li:last-child{border:none}
.btn-outline-light{border:1px solid var(--blue-soft);color:var(--blue-soft);height:37px;padding:0 18px}
.f-map{margin-top:20px;width:230px;height:240px;background:radial-gradient(ellipse at 55% 50%,#1d3f7c 0%,#132e63 45%,rgba(11,29,69,0) 75%);border-radius:4px}
.f-contact li{list-style:none;display:flex;align-items:center;gap:14px;font-size:12.5px;margin-bottom:22px}
.f-hours{font-size:12px;line-height:25px}

/* bottom badges */
.trust{height:83px;background:var(--navy-deep);border-top:1px solid rgba(255,255,255,.15);display:flex;align-items:center;justify-content:center;color:var(--white);font-size:11.5px;white-space:nowrap}
.trust span{display:flex;align-items:center;gap:10px;padding:0 22px;border-right:1px solid rgba(255,255,255,.3)}
.trust span:last-child{border:none}
.trust .corvane b{color:var(--white);font-size:18px;line-height:18px}
.trust .corvane small{color:var(--white);font-size:10.5px}
.trust .badge-square{width:30px;height:30px;background:var(--white)}
.copyright{height:53px;background:var(--navy-darkest);color:#c5cee0;font-size:11px;display:flex;align-items:center;padding-left:50px}
.copyright .legal{margin-left:172px;display:flex;gap:24px}
.copyright .legal em{font-style:normal;opacity:.5}
</style>
</head>
<body>

<div class="topbar">
  <span>Proudly based in the Whitsundays, North Queensland</span>
  <div class="contact">
    <span><svg width="12" height="12" viewBox="0 0 24 24" fill="#fff"><path d="M6.6 10.8a15 15 0 0 0 6.6 6.6l2.2-2.2a1 1 0 0 1 1-.25 11.4 11.4 0 0 0 3.6.57 1 1 0 0 1 1 1V20a1 1 0 0 1-1 1A17 17 0 0 1 3 4a1 1 0 0 1 1-1h3.5a1 1 0 0 1 1 1c0 1.25.2 2.45.57 3.57a1 1 0 0 1-.25 1z"/></svg>0400 555 019</span>
    <span><svg width="13" height="10" viewBox="0 0 26 20" fill="none" stroke="#fff" stroke-width="2"><rect x="1" y="1" width="24" height="18"/><path d="M1 1l12 10L25 1"/></svg>info@brightlinecoatings.com.au</span>
    <span class="social-square"></span>
  </div>
</div>

<header class="nav">
  <div class="brand"><div class="brand-mark"></div><div class="brand-name">BRIGHTLINE COATINGS CO</div></div>
  <nav class="menu"><span class="active">Home</span><span>About Us</span><span>ProductsGallery</span><span>Projects</span><span>Contact</span></nav>
  <span class="btn-quote-nav">Get a Quote</span>
</header>

<section class="hero">
  <div class="hero-photo" role="img" aria-label="Frameless glass pool fence beside a stone wall and tropical garden"></div>
  <div class="abs eyebrow-hero">QUALITY FABRICATION.</div>
  <h1 class="abs">BUILT TO <span class="accent">LAST.</span></h1>
  <div class="abs rule light"></div>
  <p class="abs hero-copy">Specialising in powder coated aluminium, stainless steel and glass solutions for homes and businesses across the Whitsundays and North Queensland.</p>
  <span class="abs btn btn-solid" style="left:35px">Our Products <svg width="12" height="10" viewBox="0 0 12 10" fill="none" stroke="#fff" stroke-width="1.5"><path d="M0 5h11M7 1l4 4-4 4"/></svg></span>
  <span class="abs btn btn-outline" style="left:183px">Our Products <svg width="12" height="10" viewBox="0 0 12 10" fill="none" stroke="#fff" stroke-width="1.5"><path d="M0 5h11M7 1l4 4-4 4"/></svg></span>
  <div class="abs features">
    <div class="feature" style="width:182px"><svg width="28" height="28" viewBox="0 0 28 28" fill="none" stroke="var(--blue-soft)" stroke-width="1.5"><path d="M14 2l3 3h4v4l3 3-3 3v4h-4l-3 3-3-3H7v-4l-3-3 3-3V5h4z"/><path d="M10 14l3 3 5-6"/></svg><div><h4>PREMIUM QUALITY</h4><p>Top grade materials<br>built to last.</p></div></div>
    <div class="feature" style="width:200px"><svg width="28" height="28" viewBox="0 0 28 28" fill="none" stroke="var(--blue-soft)" stroke-width="1.5"><rect x="3" y="8" width="22" height="12"/><path d="M7 8v12M11 8v12M15 8v12M19 8v12M3 4h22"/></svg><div><h4>CUSTOM FABRICATION</h4><p>Tailored solutions to<br>suit your project.</p></div></div>
    <div class="feature" style="width:215px"><svg width="28" height="28" viewBox="0 0 28 28" fill="none" stroke="var(--blue-soft)" stroke-width="1.5"><path d="M3 13L14 4l11 9M6 11v13h16V11M11 24v-7h6v7"/></svg><div><h4>DOMESTIC &amp; COMMERCIAL</h4><p>Proudly serving homes<br>and businesses.</p></div></div>
    <div class="feature" style="width:200px"><svg width="28" height="28" viewBox="0 0 28 28" fill="none" stroke="var(--blue-soft)" stroke-width="1.5"><circle cx="12" cy="9" r="5"/><path d="M3 25c0-5 4-8 9-8s9 3 9 8"/><path d="M22 13a3 3 0 0 1 3 3c0 2-3 5-3 5s-3-3-3-5a3 3 0 0 1 3-3z"/></svg><div><h4>LOCAL EXPERTS</h4><p>Based in the Whitsundays,<br>servicing North Queensland.</p></div></div>
  </div>
  <div class="abs local-card">
    <svg width="18" height="24" viewBox="0 0 18 24" fill="var(--blue-soft)"><path d="M9 0a9 9 0 0 1 9 9c0 6-9 15-9 15S0 15 0 9a9 9 0 0 1 9-9z"/><circle cx="9" cy="9" r="3.5" fill="var(--navy)"/></svg>
    <div><h4>Local to the Whitsundays</h4><p>Servicing from Airlie Beach to Townsville and surrounding areas.</p></div>
  </div>
</section>

<section class="products">
  <div class="abs intro">
    <div class="eyebrow">OUR PRODUCTS</div>
    <div class="title">FUNCTIONAL.<br>STYLISH. BUILT<br>FOR QUEENSLAND.</div>
    <div class="rule"></div>
    <p>From concept to completion, we deliver high-quality custom-made solutions using premium materials and expert craftsmanship.</p>
    <span class="btn btn-solid">View All Products <svg width="12" height="10" viewBox="0 0 12 10" fill="none" stroke="#fff" stroke-width="1.5"><path d="M0 5h11M7 1l4 4-4 4"/></svg></span>
  </div>
  <article class="abs card" style="left:333px">
    <div class="card-photo" role="img" aria-label="Cream powder coated aluminium slat privacy screen and gate" style="background:linear-gradient(180deg,#8fa6c4 0%,#c8ccd0 35%,#e5e1d6 70%,#9a9a94 100%)"></div>
    <h3>PRIVACY SCREENS</h3>
    <p>Powder coated aluminium slat screens for privacy, security and style.</p>
    <span class="more">VIEW MORE <svg width="12" height="10" viewBox="0 0 12 10" fill="none" stroke="var(--blue)" stroke-width="1.5"><path d="M0 5h11M7 1l4 4-4 4"/></svg></span>
  </article>
  <article class="abs card" style="left:615px">
    <div class="card-photo" role="img" aria-label="Glass balustrade on a timber deck among trees" style="background:linear-gradient(180deg,#4a3a2e 0%,#6b5444 40%,#5a6a56 75%,#3e4a36 100%)"></div>
    <h3>GLASS FENCING</h3>
    <p>Sleek, safe and compliant glass pool fencing solutions.</p>
    <span class="more">VIEW MORE <svg width="12" height="10" viewBox="0 0 12 10" fill="none" stroke="var(--blue)" stroke-width="1.5"><path d="M0 5h11M7 1l4 4-4 4"/></svg></span>
  </article>
  <article class="abs card" style="left:900px">
    <div class="card-photo" role="img" aria-label="Timber boardwalk with stainless steel handrails through bushland" style="background:linear-gradient(180deg,#4e6a4a 0%,#6b7d5c 40%,#8a7a66 70%,#5e6e4e 100%)"></div>
    <h3>STAINLESS STEEL HANDRAILS</h3>
    <p>Durable stainless steel handrails for a premium finish.</p>
    <span class="more">VIEW MORE <svg width="12" height="10" viewBox="0 0 12 10" fill="none" stroke="var(--blue)" stroke-width="1.5"><path d="M0 5h11M7 1l4 4-4 4"/></svg></span>
  </article>
</section>

<section class="stats">
  <div class="stats-photo" role="img" aria-label="Stainless steel handrail on an outdoor staircase"></div>
  <div class="stats-shade"></div>
  <div class="stats-navy"></div>
  <div class="abs stat" style="left:33px"><div class="num">15+</div><div class="label">YEARS EXPERIENCE</div><p>Delivering quality<br>solutions since<br>2009.</p></div>
  <div class="abs stat-divider" style="left:179px"></div>
  <div class="abs stat" style="left:207px"><div class="num">1000+</div><div class="label">PROJECTS COMPLETED</div><p>Across residential,<br>commercial &amp;<br>government sectors.</p></div>
  <div class="abs stat-divider" style="left:362px"></div>
  <div class="abs stat" style="left:390px"><div class="num">1000+</div><div class="label">PREMIUM MATERIALS</div><p>Aluminium, stainless steel<br>and safety glass built to<br>Australian standards.</p></div>
  <div class="abs stat-divider" style="left:571px"></div>
  <div class="abs stat" style="left:599px"><div class="num">1000+</div><div class="label">CUSTOM MADE</div><p>Tailored designs to<br>suit your needs<br>and style.</p></div>
  <div class="abs ready">
    <h3>READY TO START YOUR PROJECT?</h3>
    <p>Get in touch today for a free quote or expert advice.</p>
    <span class="btn btn-white">Get a Quote <svg width="12" height="10" viewBox="0 0 12 10" fill="none" stroke="var(--blue)" stroke-width="1.5"><path d="M0 5h11M7 1l4 4-4 4"/></svg></span>
    <span class="btn btn-outline" style="margin-left:14px"><svg width="12" height="12" viewBox="0 0 24 24" fill="#fff"><path d="M6.6 10.8a15 15 0 0 0 6.6 6.6l2.2-2.2a1 1 0 0 1 1-.25 11.4 11.4 0 0 0 3.6.57 1 1 0 0 1 1 1V20a1 1 0 0 1-1 1A17 17 0 0 1 3 4a1 1 0 0 1 1-1h3.5a1 1 0 0 1 1 1c0 1.25.2 2.45.57 3.57a1 1 0 0 1-.25 1z"/></svg>0400 555 019</span>
  </div>
</section>

<section class="serving">
  <h4>PROWEDLY SERVING</h4>
  <div class="badges-row">
    <span><i class="badge-square"></i>AUSTRALIAN MADE</span>
    <span><svg width="22" height="22" viewBox="0 0 22 22" fill="none" stroke="var(--blue)" stroke-width="1.5"><circle cx="11" cy="11" r="10"/><path d="M6 11l3.5 3.5L16 8"/></svg>AS/NZS COMPLIANT</span>
    <span class="corvane" style="margin-left:14px"><b>Corvane</b><small>POWDER COATINGS</small></span>
    <span><i class="badge-shape"></i>Marine Grade</span>
  </div>
</section>

<section class="about">
  <div class="about-photo" role="img" aria-label="Glass pool fence with spigots on a stone paved terrace and garden"></div>
  <div class="abs about-text">
    <div class="eyebrow">ABOUT US</div>
    <div class="title">DESIGN. FABRICATE. INSTALL.<br><span class="blue">DELIVER.</span></div>
    <div class="rule"></div>
    <p>We are a family-owned and operated business in the Whitsundays, specialising in the design, fabrication and installation of powder coated aluminium, stainless steel and glass products.</p>
    <p>From concept to completion, we take pride in our workmanship and attention to detail.</p>
  </div>
</section>

<section class="process">
  <div class="eyebrow">OUR PROCESS</div>
  <h2>QUALITY THROUGH EVERY STEP</h2>
  <div class="abs step" style="left:146px"><div class="step-circle"><svg width="28" height="26" viewBox="0 0 28 26" fill="none" stroke="#fff" stroke-width="1.4"><path d="M12 4h13v10h-4l-3 3v-3h-6z"/><path d="M3 10h7v8H7l-2 2v-2H3z"/></svg></div><div class="step-num">01</div><h3>CONSULTATION</h3><p>We listen to your ideas and understand your needs.</p></div>
  <div class="abs step" style="left:372px"><div class="step-circle"><svg width="26" height="26" viewBox="0 0 26 26" fill="none" stroke="#fff" stroke-width="1.4"><path d="M5 21l4-12 8 8z"/><path d="M9 9l4-6 10 10-6 4"/><circle cx="12" cy="15" r="1.5"/></svg></div><div class="step-num">02</div><h3>DESIGN</h3><p>Thoughtful, functional designs tailored to your space.</p></div>
  <div class="abs step" style="left:599px"><div class="step-circle"><svg width="28" height="22" viewBox="0 0 28 22" fill="none" stroke="#fff" stroke-width="1.4"><rect x="3" y="6" width="22" height="10"/><path d="M7 6v10M11 6v10M15 6v10M19 6v10M3 3h22M3 19h22"/></svg></div><div class="step-num">03</div><h3>FABRICATION</h3><p>Precision manufactured in-house using premium materials.</p></div>
  <div class="abs step" style="left:825px"><div class="step-circle"><svg width="26" height="26" viewBox="0 0 26 26" fill="none" stroke="#fff" stroke-width="1.4"><circle cx="13" cy="13" r="5"/><path d="M13 2v4M13 20v4M2 13h4M20 13h4M5 5l3 3M18 18l3 3M5 21l3-3M18 8l3-3"/></svg></div><div class="step-num">04</div><h3>INSTALLATION</h3><p>Expert installation by our experienced team.</p></div>
  <div class="abs step" style="left:1055px"><div class="step-circle"><svg width="24" height="24" viewBox="0 0 24 24" fill="none" stroke="#fff" stroke-width="1.4"><circle cx="12" cy="12" r="10"/><path d="M7 12l3.5 3.5L17 9"/></svg></div><div class="step-num">05</div><h3>COMPLETION</h3><p>Built to last with quality you can trust.</p></div>
</section>

<section class="cta">
  <div class="cta-photo" role="img" aria-label="Faded coastal garden with glass fencing"></div>
  <div class="abs cta-text">
    <div class="title">LET'S BRING YOUR<br><span class="blue">VISION TO LIFE.</span></div>
    <div class="rule"></div>
    <p>Whether it's a custom home or a commercial project, we're here to bring your ideas to life with quality craftsmanship and exceptional service.</p>
  </div>
  <span class="abs btn btn-solid" style="left:666px"><svg width="18" height="16" viewBox="0 0 18 16" fill="none" stroke="#fff" stroke-width="1.4"><path d="M1 1h16v11H6l-4 3v-3H1z"/><path d="M5 5h8M5 8h6"/></svg>GET A QUOTE <svg width="18" height="12" viewBox="0 0 18 12" fill="none" stroke="#fff" stroke-width="1.6"><path d="M0 6h17M12 1l5 5-5 5"/></svg></span>
  <span class="abs btn btn-outline-blue" style="left:891px"><svg width="18" height="16" viewBox="0 0 18 16" fill="none" stroke="var(--blue)" stroke-width="1.4"><path d="M1 1h16v11H6l-4 3v-3H1z"/><path d="M5 5h8M5 8h6"/></svg>GET A QUOTE <svg width="18" height="12" viewBox="0 0 18 12" fill="none" stroke="var(--blue)" stroke-width="1.6"><path d="M0 6h17M12 1l5 5-5 5"/></svg></span>
  <div class="abs cta-feats">
    <span><svg width="26" height="24" viewBox="0 0 26 24" fill="none" stroke="var(--blue)" stroke-width="1.4"><path d="M3 3h20v14H10l-5 4v-4H3z"/><path d="M7 8h12M7 12h8"/></svg>FREE QUOTES</span>
    <span><svg width="20" height="20" viewBox="0 0 20 20" fill="none" stroke="var(--navy)" stroke-width="1.5"><path d="M4 5a8 8 0 1 1-1 5"/><path d="M4 1v4h4"/></svg>QUICK TURNAROUND</span>
    <span><svg width="20" height="22" viewBox="0 0 20 22" fill="none" stroke="var(--navy)" stroke-width="1.5"><path d="M10 1l8 3v6c0 6-4 9-8 11-4-2-8-5-8-11V4z"/><path d="M6 11l3 3 5-6"/></svg>QUALITY GUARANTEE</span>
  </div>
</section>

<footer class="footer">
  <div class="abs f-col" style="left:34px;width:220px">
    <div class="f-mark"></div>
    <div class="f-brand-name">BRIGHTLINE COATINGS CO</div>
    <div class="f-brand-sub">WHITSUNDAYS</div>
    <div class="rule"></div>
    <div class="f-about"><p>We are a family business based in the Whitsundays, specialising in the design, fabrication and installation of powder coated aluminium, stainless steel and glass products.</p><p>Proudly servicing from Airlie Beach to Townsville and surrounding areas.</p></div>
    <div class="f-socials"><i></i><i></i><i></i></div>
  </div>
  <div class="abs f-divider" style="left:290px"></div>
  <div class="abs f-col" style="left:316px">
    <h4>SERVICING</h4>
    <ul class="f-links">
      <li>Privacy Screens<span>›</span></li>
      <li>Balustrades<span>›</span></li>
      <li>Glass Fencing<span>›</span></li>
      <li>Stainless Steel HandrailsP<span>›</span></li>
      <li>owder Coated Aluminium Handrails<span>›</span></li>
      <li>Pool Fencing &amp; Gates<span>›</span></li>
    </ul>
    <span class="btn btn-outline-light" style="margin-top:58px;margin-left:3px">View All Products <svg width="12" height="10" viewBox="0 0 12 10" fill="none" stroke="var(--blue-soft)" stroke-width="1.5"><path d="M0 5h11M7 1l4 4-4 4"/></svg></span>
  </div>
  <div class="abs f-divider" style="left:574px"></div>
  <div class="abs f-col" style="left:599px">
    <h4>SERVICING</h4>
    <p style="font-size:12px;line-height:25px;margin-top:28px;width:230px">Proudly servicing from Airlie Beach to Townsville and surrounding areas.</p>
    <div class="f-map" role="img" aria-label="Coastline map from Townsville to Airlie Beach with service locations"></div>
  </div>
  <div class="abs f-divider" style="left:858px"></div>
  <div class="abs f-col" style="left:883px">
    <h4>CONTACT US</h4>
    <ul class="f-contact" style="margin-top:30px">
      <li><svg width="16" height="16" viewBox="0 0 24 24" fill="none" stroke="#fff" stroke-width="1.5"><path d="M6.6 10.8a15 15 0 0 0 6.6 6.6l2.2-2.2a1 1 0 0 1 1-.25 11.4 11.4 0 0 0 3.6.57 1 1 0 0 1 1 1V20a1 1 0 0 1-1 1A17 17 0 0 1 3 4a1 1 0 0 1 1-1h3.5a1 1 0 0 1 1 1c0 1.25.2 2.45.57 3.57a1 1 0 0 1-.25 1z"/></svg>0400 555 019</li>
      <li><svg width="17" height="13" viewBox="0 0 26 20" fill="none" stroke="#fff" stroke-width="1.8"><rect x="1" y="1" width="24" height="18"/><path d="M1 1l12 10L25 1"/></svg>info@brightlinecoatings.com.au</li>
      <li><svg width="14" height="18" viewBox="0 0 18 24" fill="none" stroke="#fff" stroke-width="1.6"><path d="M9 1a8 8 0 0 1 8 8c0 6-8 14-8 14S1 15 1 9a8 8 0 0 1 8-8z"/><circle cx="9" cy="9" r="3"/></svg>Baymont, QLD 4799</li>
    </ul>
    <h4 style="margin-top:50px">BUSINESS HOURS</h4>
    <div class="rule" style="margin:16px 0 14px"></div>
    <div class="f-hours">Monday – Friday : 7:00am – 4:00pm<br>Saturday - By Appointment</div>
    <span class="btn btn-outline-light" style="margin-top:36px">GET A QUOTE <svg width="12" height="10" viewBox="0 0 12 10" fill="none" stroke="var(--blue-soft)" stroke-width="1.5"><path d="M0 5h11M7 1l4 4-4 4"/></svg></span>
  </div>
</footer>

<div class="trust">
  <span><i class="badge-square"></i>AUSTRALIAN MADE</span>
  <span><svg width="30" height="30" viewBox="0 0 30 30" fill="none" stroke="#fff" stroke-width="1.5"><circle cx="15" cy="15" r="13"/><path d="M9 15l4 4 8-8"/></svg>AS/NZS COMPLIANT</span>
  <span class="corvane"><b>Corvane</b><small>POWDER COATINGS</small></span>
  <span><svg width="30" height="30" viewBox="0 0 30 30" fill="none" stroke="#fff" stroke-width="1.5"><circle cx="15" cy="15" r="13"/><path d="M5 17c3-2 6 2 10 0s7-2 10 0M5 22c3-2 6 2 10 0s7-2 10 0"/></svg>MARINE GRADE</span>
  <span><svg width="26" height="30" viewBox="0 0 26 30" fill="none" stroke="#fff" stroke-width="1.5"><path d="M13 2l10 4v8c0 8-5 12-10 14C8 26 3 22 3 14V6z"/><path d="M8 15l4 4 6-7"/></svg>PREMIUM MATERIALS</span>
  <span><svg width="30" height="30" viewBox="0 0 30 30" fill="none" stroke="#fff" stroke-width="1.5"><path d="M4 26L18 12M20 4a6 6 0 0 0-4 9l2 2a6 6 0 0 0 9-4l-3 1-3-3zM26 26L12 12M4 4l4 4"/></svg>EXPERT CRAFTSMANSHIP</span>
</div>

<div class="copyright">
  <span>© Brightline Coatings Co. All Rights Reserved.</span>
  <div class="legal"><span>Privacy Policy</span><em>|</em><span>Terms &amp; Conditions</span><em>|</em><span>Sitemap</span></div>
</div>

</body>
</html>
```